San Francisco Leading Consulting firm - 47Vora Web Design Project

•Create a Web Design
•Uncoded webpage layout design
•2 Pages Design - Homepage + Interior Page

Task Description
Hello, we're looking for a re-design our current website www.47vora-example.com

we have a sample mockup design @

http://47vora.pubtrellis-example.org/

This shows the layout that we like and also a sample of 6 pictures that would change based on where you mouse over..

6 pictures HOME design needs to be included.

SMART
THOUGHTFUL
FLEXIBLE
CREATIVE SERVICES
TECHNICAL SERVICES
PARTNERS

sites we like:

http://www.melvanadvisory-example.com/Home.cfm?id=Home
http://www.plinthworks-example.com/index.html

Our company can be best described as: 100+ employees, cutting-edge, depandable, innovative, strong, smart.

Our Primary focus is: IT Consulting Services and Creative Design services

47Vora LLC is a consulting firm providing creative design, business and technology solutions to both private and public interests.

Established in 1996, 47Vora is a San Francisco based company providing specialists for a range of business needs including:

Creative Design Services
•Print
•Logo Design
•Website Design
•Illustration

and

Business and Technology solutions

•Application Software and Web Development
•Business Process Re-Design (BPR)
•Business/Systems Analysis and Requirement Documentation
•Mentoring and Training
•Network/Hardware Installation Services
•System Design and Architecture
•Vendor Management
•Docuvault Architecture and Implementation

our sample mockup site:

Reason: Due to holiday season, we're not available to work with designers and finilize our design.  

Thank you very much for submitting your design.

We appreciate your time and creativity.   Since, our office is currently closed for holidays, we will be reviewing it in details next week and will make our decision as soon as possible.

It would be great if you could submit any of your changes by Wed next week, so it would be part of our reviews. 

Please see updated wireframe under attachments:  we have some minor updates to our wireframe that we would like you to update your designs, if possible.  

We also encorouge you not to use our standard wireframe and come up with more unique designs.   Everything would be considered when we review your design.

 

Ringmark Market(s)

Creative services and professional services clients, including government agencies

Industry/Entity Type

Business

Requirements
Must have
• Clean, professional look, easy navigation

```html
<!DOCTYPE html>
<html lang="en">
<head>
<meta charset="utf-8">
<title>47Vora — Consulting, Creative &amp; Technical Services</title>
<link href="https://fonts.googleapis.com/css2?family=Arimo:wght@400;700&family=Roboto+Condensed:wght@700&display=swap" rel="stylesheet">
<style>
  :root{
    --blue:#0a8fc8;
    --blue-dark:#0679b0;
    --blue-light:#5cc3ea;
    --ink:#333;
    --grey:#555;
    --grey-mid:#777;
    --rule:#d8d8d8;
    --sky:#e9e9e9;
    --city-mid:#b4b4b4;
    --city-dark:#6e6e6e;
    --white:#fff;
  }
  *{box-sizing:border-box;margin:0;padding:0}
  html,body{width:1200px;height:960px;overflow:hidden;background:var(--white)}
  body{position:relative;font-family:"Arimo",Arial,sans-serif;color:var(--ink)}

  .site-header{position:absolute;left:0;top:0;width:1200px;height:92px;border-bottom:2px solid var(--blue)}
  .brand{position:absolute;left:170px;top:26px;display:flex;align-items:center;gap:10px;text-decoration:none}
  .brand-mark{width:34px;height:34px;border-radius:50%;background:var(--blue)}
  .brand-name{font-size:30px;font-weight:400;color:var(--grey);letter-spacing:1px}
  .main-nav{position:absolute;left:381px;top:37px;display:flex}
  .main-nav a{font-size:12.5px;font-weight:700;color:var(--ink);text-decoration:none;padding:0 11px 0 10px;line-height:18px;border-left:1px solid var(--blue)}
  .main-nav a:first-child{border-left:0}
  .contact-block{position:absolute;left:929px;top:12px;font-size:12px;line-height:18px;color:var(--ink);font-style:normal}
  .contact-block .accent{color:var(--blue);font-weight:700}

  .hero{position:absolute;left:0;top:92px;width:1200px;height:528px}
  .hero-backdrop{position:absolute;inset:0;background:
      linear-gradient(90deg,rgba(90,90,90,.25) 0%,rgba(255,255,255,0) 12%,rgba(255,255,255,0) 88%,rgba(90,90,90,.25) 100%),
      linear-gradient(180deg,#d4d4d4 0%,var(--sky) 14%,#dadada 38%,var(--city-mid) 62%,#9a9a9a 80%,var(--city-dark) 100%)}
  .slider{position:absolute;left:118px;top:45px;width:960px;height:349px;border-radius:3px 3px 0 0;overflow:hidden;background:linear-gradient(180deg,#0a8dc6 0%,#1d9fd6 40%,#5cb9e0 70%,#2d9fd3 100%)}
  .slide-photo{position:absolute;left:0;top:0}
  .slide-copy{position:absolute;left:110px;top:94px;font-family:"Roboto Condensed","Arial Narrow",sans-serif;font-weight:700;color:var(--white);text-transform:uppercase;text-shadow:1px 2px 3px rgba(0,0,0,.35)}
  .slide-title{font-size:52px;line-height:56px;letter-spacing:-.5px}
  .slide-lede{font-size:24.5px;line-height:28px;margin-top:-2px}
  .slide-arrow{position:absolute;top:157px}
  .slide-arrow.prev{left:20px}
  .slide-arrow.next{right:20px}
  .slider-dots{position:absolute;left:118px;top:394px;width:960px;height:46px;background:rgba(255,255,255,.55);display:flex;justify-content:center;align-items:center;gap:14px}
  .slider-dots span{width:14px;height:14px;border-radius:50%;background:#000}
  .slider-dots span.active{background:var(--blue)}

  .clients{position:absolute;left:120px;top:620px;width:960px;height:88px;border-bottom:1px solid var(--rule);display:flex;align-items:center}
  .clients-label{font-size:20px;font-weight:700;line-height:24px;color:var(--ink);margin-left:6px;width:108px}
  .clients-arrow{margin-right:26px}
  .client-list{display:flex;justify-content:space-between;align-items:center;flex:1;padding-right:6px}
  .client{display:flex;align-items:center;gap:5px;font-size:14px;font-weight:700;color:var(--grey-mid)}
  .client i{width:12px;height:12px;border-radius:50%;background:var(--grey-mid)}

  .service-cards{position:absolute;left:120px;top:734px;width:960px;height:100px}
  .service-card{position:absolute;top:0;width:280px;height:100px;border:1px solid #bbb;border-radius:4px;overflow:hidden;background:var(--white)}
  .card-creative{left:0}
  .card-technical{left:338px}
  .card-partners{left:673px}
  .service-card h2{position:absolute;left:6px;top:4px;font-size:15px;font-weight:400;color:var(--grey)}
  .card-art{position:absolute}
  .art-creative{left:80px;top:26px;width:148px;height:74px;border-radius:50px 50px 0 0;background:linear-gradient(90deg,#c86fd6,#f0a6c8 35%,#f2d35a 60%,#6cc9e6)}
  .art-technical{left:44px;top:28px;width:164px;height:72px;border-radius:36px 36px 0 0;background:radial-gradient(circle at 50% 40%,#e2e2e2,#a4a4a4 60%,#8a8a8a)}
  .art-partners{left:86px;top:8px;width:142px;height:86px;border-radius:10px;background:linear-gradient(90deg,#bfe3f3,#f6c4e0 50%,#d4eeb6)}
  .card-corner{position:absolute;right:0;bottom:0}

  .site-footer{position:absolute;left:120px;top:857px;width:960px;border-top:1px solid var(--rule)}
  .copyright{position:absolute;left:2px;top:17px;font-size:12px;color:var(--ink)}
  .footer-nav{position:absolute;right:7px;top:18px;display:flex;gap:30px}
  .footer-nav a{font-size:12px;font-weight:700;color:var(--ink);text-decoration:none}
</style>
</head>
<body>
  <header class="site-header">
    <a class="brand" href="#"><span class="brand-mark"></span><span class="brand-name">47Vora</span></a>
    <nav class="main-nav">
      <a href="#">Company</a>
      <a href="#">Creative Services</a>
      <a href="#">Technical Services</a>
      <a href="#">Partners</a>
      <a href="#">Contact Us</a>
    </nav>
    <address class="contact-block">
      2258 Larkin Row, Ste 804<br>
      San Francisco, CA 94109<br>
      <span class="accent">415-555-0147</span><br>
      <span class="accent">info@47vora-example.com</span>
    </address>
  </header>

  <section class="hero">
    <div class="hero-backdrop" role="img" aria-label="Black and white aerial view of the San Francisco skyline"></div>
    <div class="slider">
      <svg class="slide-photo" width="960" height="349" role="img" aria-label="Close-up photograph of a microchip on a circuit board">
        <defs>
          <linearGradient id="chipTone" x1="0" y1="0" x2="0" y2="1">
            <stop offset="0" stop-color="#c4a679"/>
            <stop offset="0.25" stop-color="#8fa3b4"/>
            <stop offset="0.55" stop-color="#5d6673"/>
            <stop offset="0.8" stop-color="#6f7d6a"/>
            <stop offset="1" stop-color="#4d7a62"/>
          </linearGradient>
        </defs>
        <polygon points="460,0 828,0 868,349 492,349" fill="url(#chipTone)"/>
      </svg>
      <div class="slide-copy">
        <div class="slide-title">Technical</div>
        <div class="slide-lede">Our capabilities range from<br>application development<br>to vendor management</div>
      </div>
      <svg class="slide-arrow prev" width="28" height="50" aria-hidden="true"><polyline points="24,3 6,25 24,47" fill="none" stroke="#fff" stroke-width="6"/></svg>
      <svg class="slide-arrow next" width="28" height="50" aria-hidden="true"><polyline points="4,3 22,25 4,47" fill="none" stroke="#fff" stroke-width="6"/></svg>
    </div>
    <div class="slider-dots">
      <span></span><span class="active"></span><span></span><span></span><span></span><span></span>
    </div>
  </section>

  <section class="clients">
    <h2 class="clients-label">Featured Clients</h2>
    <svg class="clients-arrow" width="20" height="36" aria-hidden="true"><polyline points="4,2 16,18 4,34" fill="none" stroke="var(--blue)" stroke-width="5"/></svg>
    <div class="client-list">
      <span class="client"><i></i>Ringmark</span>
      <span class="client">Dunmere</span>
      <span class="client">Delvo</span>
      <span class="client">Gavrin</span>
      <span class="client">Faxton</span>
      <span class="client">Veranto</span>
      <span class="client">Civara</span>
      <span class="client">Jorvik Fields</span>
      <span class="client">Colvane</span>
    </div>
  </section>

  <section class="service-cards">
    <article class="service-card card-creative">
      <h2>Creative Services</h2>
      <div class="card-art art-creative" role="img" aria-label="Colourful abstract flowing ribbon illustration"></div>
      <svg class="card-corner" width="42" height="42" aria-hidden="true"><polygon points="42,0 42,42 0,42" fill="var(--blue)"/><path d="M27 28h10M32 23v10" stroke="#fff" stroke-width="2"/></svg>
    </article>
    <article class="service-card card-technical">
      <h2>Business &amp; Technical Services</h2>
      <div class="card-art art-technical" role="img" aria-label="Illustration of interlocking metal gears"></div>
      <svg class="card-corner" width="42" height="42" aria-hidden="true"><polygon points="42,0 42,42 0,42" fill="var(--blue)"/><path d="M27 28h10M32 23v10" stroke="#fff" stroke-width="2"/></svg>
    </article>
    <article class="service-card card-partners">
      <h2>Partners</h2>
      <div class="card-art art-partners" role="img" aria-label="Map of the United States drawn as coloured transit lines"></div>
      <svg class="card-corner" width="42" height="42" aria-hidden="true"><polygon points="42,0 42,42 0,42" fill="var(--blue)"/><path d="M27 28h10M32 23v10" stroke="#fff" stroke-width="2"/></svg>
    </article>
  </section>

  <footer class="site-footer">
    <p class="copyright">Copyright 2011, 47Vora, LLC All rights reserved.</p>
    <nav class="footer-nav">
      <a href="#">Home</a>
      <a href="#">Company</a>
      <a href="#">Technical Services</a>
      <a href="#">Creative Services</a>
      <a href="#">Partners</a>
      <a href="#">Contact Us</a>
    </nav>
  </footer>
</body>
</html>
```